FunBrixo Business Card

We need a business card design for our company. We sell construction-themed amusement rides for kids.

Contact Information for Business Card

Contact info on business card should include:
Carl Dunning
Co-Founder & COO
(833) 571-FUNBRIX
Carl@funbrixo-demo.com
www.funbrixo-demo.com

```html
<!DOCTYPE html>
<html lang="en">
<head>
<meta charset="utf-8">
<title>FunBrixo Business Card</title>
<link rel="stylesheet" href="https://fonts.googleapis.com/css2?family=Open+Sans:wght@400;600;700&display=swap">
<style>
  :root {
    --stage: #3a3b3e;
    --brand-yellow: #fdc114;
    --brand-orange: #e8552b;
    --ink: #1d1d1d;
    --paper-light: #ffffff;
    --paper-shade: #d9d9d9;
    --text-white: #ffffff;
    --figure-tone-a: #f3c53a;
    --figure-tone-b: #e9e9e9;
  }
  * { margin: 0; padding: 0; box-sizing: border-box; }
  html, body { width: 1200px; height: 900px; overflow: hidden; }
  body {
    background: var(--stage);
    font-family: "Open Sans", Arial, sans-serif;
    position: relative;
  }
  .card {
    position: absolute;
    width: 700px;
    height: 400px;
    border-radius: 34px;
    overflow: hidden;
    box-shadow: 0 12px 30px rgba(0,0,0,0.45);
  }

  /* Back side */
  .card-back {
    left: 110px;
    top: 40px;
    background: var(--brand-yellow);
  }
  .brand-mark {
    position: absolute;
    left: 0; right: 0;
    top: 150px;
    display: flex;
    align-items: center;
    justify-content: center;
    gap: 14px;
  }
  .brand-dot {
    width: 34px; height: 34px;
    border-radius: 50%;
    background: var(--brand-orange);
  }
  .brand-name {
    font-size: 52px;
    font-weight: 700;
    color: var(--brand-orange);
    letter-spacing: 0.5px;
  }
  .back-website {
    position: absolute;
    left: 0; right: 0;
    top: 290px;
    text-align: center;
    font-size: 19px;
    font-weight: 700;
    color: var(--text-white);
    letter-spacing: 0.5px;
  }

  /* Front side */
  .card-front {
    left: 390px;
    top: 470px;
    background: linear-gradient(160deg, var(--paper-shade) 0%, var(--paper-light) 45%, var(--paper-shade) 100%);
  }
  .name-block {
    position: absolute;
    right: 44px;
    top: 36px;
    text-align: left;
  }
  .name-row { display: flex; }
  .name-first, .name-last {
    font-size: 28px;
    font-weight: 600;
    color: var(--text-white);
    padding: 4px 14px;
    line-height: 1.2;
  }
  .name-first { background: var(--ink); }
  .name-last { background: var(--brand-yellow); }
  .job-title {
    margin-top: 6px;
    font-size: 15px;
    font-weight: 700;
    color: var(--ink);
    letter-spacing: 0.3px;
  }
  .crew-illustration {
    position: absolute;
    right: 40px;
    top: 130px;
    width: 250px;
    height: 240px;
    border-radius: 18px;
    background: linear-gradient(180deg, var(--figure-tone-a) 0%, var(--figure-tone-b) 60%, rgba(233,233,233,0) 100%);
  }
  .contact-list {
    position: absolute;
    left: 70px;
    bottom: 50px;
    list-style: none;
  }
  .contact-item {
    display: flex;
    align-items: center;
    gap: 12px;
    font-size: 18px;
    color: var(--ink);
    line-height: 1.65;
  }
  .contact-icon { width: 16px; height: 16px; flex: none; }
</style>
</head>
<body>

<section class="card card-back" aria-label="Card back">
  <div class="brand-mark">
    <span class="brand-dot"></span>
    <span class="brand-name">FunBrixo</span>
  </div>
  <p class="back-website">www.funbrixo-demo.com</p>
</section>

<section class="card card-front" aria-label="Card front">
  <div class="name-block">
    <div class="name-row">
      <span class="name-first">CARL</span>
      <span class="name-last">DUNNING</span>
    </div>
    <p class="job-title">CO-FOUNDER &amp; COO</p>
  </div>

  <div class="crew-illustration" role="img" aria-label="Illustration of two cartoon construction workers in yellow hard hats standing side by side"></div>

  <ul class="contact-list">
    <li class="contact-item">
      <svg class="contact-icon" viewBox="0 0 16 16" aria-hidden="true">
        <rect x="4" y="1" width="8" height="14" rx="1.5" fill="none" stroke="var(--brand-yellow)" stroke-width="1.6"/>
        <circle cx="8" cy="12.3" r="0.9" fill="var(--brand-yellow)"/>
      </svg>
      <span>(833) 571-FUNBRIX</span>
    </li>
    <li class="contact-item">
      <svg class="contact-icon" viewBox="0 0 16 16" aria-hidden="true">
        <rect x="1" y="3" width="14" height="10" fill="var(--brand-yellow)"/>
        <path d="M1 3 L8 9 L15 3" fill="none" stroke="var(--paper-light)" stroke-width="1.3"/>
      </svg>
      <span>Carl@funbrixo-demo.com</span>
    </li>
    <li class="contact-item">
      <svg class="contact-icon" viewBox="0 0 16 16" aria-hidden="true">
        <g fill="none" stroke="var(--brand-yellow)" stroke-width="1.4">
          <circle cx="8" cy="8" r="6.5"/>
          <ellipse cx="8" cy="8" rx="3" ry="6.5"/>
          <line x1="1.5" y1="8" x2="14.5" y2="8"/>
        </g>
      </svg>
      <span>www.funbrixo-demo.com</span>
    </li>
  </ul>
</section>

</body>
</html>
```